Boutique Real Estate Brokerage Tessly Realty Website Design

Winning designer work on migrate as well through nest ferry.
We need a new website as an informational hub to aid our print and digital strategy as well as showing that we are located in Brooklyn and Florida. I have a boutique real estate brokerage and advisory firm specializing in residential leasing, multifamily sales and 1031 Exchange appropriation. This won't be a portal to search properties, it will be a place for information. I'd like space for an ebook to be downloaded and information on my probate sales and multifamily leasing marketing campaigns. I included my logo and will leave it up to the designer to come up with colors to match it. I have also attached verbiage for each page. The final design should have a modern high end look that reflects gentrifying Brooklyn as well as beautiful Florida.
Thank you!
Target Market(s)
Owners of income producing real estate and develop-able land in Brooklyn, NY and Florida.
Industry/Entity Type
Real Estate
Coding
Coded - Design and coding required
Number of Pages Required
5+ page
Colors
Designer to choose colors to be used in the design.
Requirements
Must have
- A modern elegant look
Nice to have
- pictures of brooklyn and florida
Should not have
- real estate search pages

```html
<!DOCTYPE html>
<html lang="en">
<head>
<meta charset="utf-8">
<title>Tessly Realty</title>
<link href="https://fonts.googleapis.com/css2?family=Montserrat:wght@500;600;700;800&family=Lato:ital,wght@0,400;0,700;1,400&display=swap" rel="stylesheet">
<style>
:root{
  --black:#000;
  --ink:#111;
  --white:#fff;
  --grey-band:#e9e9e9;
  --text:#333;
  --field:#e4e4e4;
  --ebook:#262626;
}
*{margin:0;padding:0;box-sizing:border-box}
html,body{width:1200px;height:3965px;overflow:hidden}
body{font-family:"Lato",sans-serif;color:var(--text);background:var(--white);position:relative}
.abs{position:absolute}
h2{font-family:"Montserrat",sans-serif;font-weight:800;text-transform:uppercase}

/* header */
.site-header{left:0;top:0;width:1200px;height:87px;background:var(--black)}
.brand{display:flex;align-items:center;gap:12px;color:var(--white);font-family:"Montserrat",sans-serif;font-weight:600;font-size:14px;letter-spacing:2px}
.brand-mark{width:36px;height:36px;background:#9a9a9a}
.site-header .brand{position:absolute;left:192px;top:25px}
.main-nav{position:absolute;right:215px;top:35px;display:flex;gap:30px}
.main-nav a{color:var(--white);text-decoration:none;font-family:"Montserrat",sans-serif;font-weight:700;font-size:14px}

/* hero */
.hero{left:0;top:87px;width:1200px;height:621px;overflow:hidden;
  background:
   linear-gradient(180deg,rgba(0,0,0,.15),rgba(0,0,0,.35)),
   radial-gradient(ellipse 300px 120px at 12% 20%,#c9d3dc 0%,rgba(201,211,220,0) 100%),
   linear-gradient(180deg,#3f6ea6 0%,#6f93bb 28%,#8b8a6e 45%,#4f5a3a 58%,#3a3f33 68%,#3c4f5e 80%,#1f2e3a 100%)}
.hero-title{position:absolute;left:0;right:0;top:252px;text-align:center;color:var(--white);font-family:"Montserrat",sans-serif;font-weight:800;font-size:30px;line-height:42px;text-transform:uppercase}
.hero-slant{position:absolute;left:0;bottom:0}
.chev{position:absolute}

/* help */
.section-title{position:absolute;left:0;width:1200px;text-align:center;font-family:"Montserrat",sans-serif;font-weight:800;font-size:30px;text-transform:uppercase}
.service{position:absolute;top:819px;width:267px}
.service .photo{height:246px}
.service p{text-align:center;margin-top:18px;font-family:"Montserrat",sans-serif;font-weight:700;font-size:14px;color:var(--ink);text-transform:uppercase}

/* mortgage */
.mortgage{left:0;top:1208px;width:1200px;height:357px;
  background:
   radial-gradient(ellipse 260px 200px at 5% 45%,rgba(196,140,70,.55),rgba(0,0,0,0)),
   linear-gradient(180deg,rgba(0,0,0,0) 55%,rgba(0,0,0,.35) 100%),
   linear-gradient(90deg,#3d3227 0%,#2a2a2d 35%,#3a3a3e 70%,#2b2b2e 100%)}
.mortgage .section-title{color:var(--white);top:97px}
.calc{position:absolute;left:177px;top:158px;width:843px;height:117px;background:var(--white);border-radius:6px;display:flex;align-items:center;padding:0 27px;gap:8px}
.calc .field{width:313px;height:46px;background:var(--field);border:1px solid #d0d0d0;border-radius:3px;display:flex;align-items:center;justify-content:space-between;padding:0 20px;font-size:14px;color:#888}
.calc .field::after{content:"";border:5px solid transparent;border-top-color:#888;margin-top:5px}
.calc .btn{margin-left:2px;width:148px;height:46px;background:var(--black);color:var(--white);border-radius:3px;font-family:"Montserrat",sans-serif;font-weight:700;font-size:14px;display:flex;align-items:center;justify-content:center}

/* feature cards */
.feature{position:absolute;top:1633px;width:423px;height:421px}
.feature .label{position:absolute;left:30px;bottom:42px;color:var(--white);font-family:"Montserrat",sans-serif;font-weight:800;font-size:20px;text-decoration:underline;text-underline-offset:5px;text-transform:uppercase}
.feature svg{position:absolute;right:48px;bottom:28px}

/* story */
.story{left:0;top:2133px;width:1200px;height:515px;
  background:linear-gradient(180deg,#ececec 0%,#e9e9e9 60%,#d9d9d9 85%,#cfcfcf 100%)}
.story .photo{position:absolute;left:172px;top:85px;width:462px;height:359px}
.story-body{position:absolute;left:671px;top:85px;width:352px}
.story-body h2{font-size:30px;color:var(--ink);margin-bottom:14px}
.story-body p{font-size:12px;line-height:21.5px;color:var(--text)}
.btn-outline{display:inline-flex;align-items:center;justify-content:center;border:1.5px solid var(--ink);border-radius:6px;font-family:"Montserrat",sans-serif;font-weight:700;font-size:12px;color:var(--ink);text-transform:uppercase}
.story-body .btn-outline{margin-top:18px;width:113px;height:38px}

/* ebook */
.ebook-body{left:172px;top:2790px;width:470px}
.ebook-body h2{font-size:29px;line-height:42px;color:var(--ink)}
.ebook-body p{margin-top:22px;font-size:11.5px;line-height:21px;color:var(--text)}
.ebook-body .btn-outline{margin-top:20px;width:113px;height:38px}
.ebook-ring{left:727px;top:2750px;width:345px;height:345px;border-radius:50%;border:1px solid #ececec;background:#fbfbfb}
.ebook-cover{left:770px;top:2815px;width:250px;height:205px;background:linear-gradient(135deg,#3a3a3a,var(--ebook) 60%,#151515);transform:skewY(-18deg) rotate(12deg);box-shadow:6px 8px 14px rgba(0,0,0,.25)}

/* reviews */
.reviews{left:0;top:3198px;width:1200px;height:389px;
  background:
   linear-gradient(180deg,rgba(0,0,0,.1) 0%,rgba(0,0,0,0) 40%,rgba(0,0,0,.4) 100%),
   radial-gradient(ellipse 220px 160px at 8% 70%,rgba(150,110,70,.45),rgba(0,0,0,0)),
   linear-gradient(90deg,#2f2a26 0%,#252528 45%,#38383d 100%)}
.reviews .section-title{color:var(--white);top:60px}
.stars{position:absolute;left:326px;top:150px;color:var(--white);font-size:15px;letter-spacing:2px}
.avatar{position:absolute;left:203px;top:172px;width:106px;height:106px;border-radius:50%;background:radial-gradient(circle,#c9805a 0%,#8a6a45 55%,#5f7a4a 100%)}
.quote{position:absolute;left:322px;top:178px;width:660px;color:#eee;font-style:italic;font-size:15px;line-height:27px}
.reviewer{position:absolute;left:322px;top:297px;color:var(--white);font-family:"Montserrat",sans-serif;font-weight:700;font-size:12px;display:flex;gap:36px}

/* footer */
.site-footer{left:0;top:3587px;width:1200px;height:378px;background:var(--black);color:var(--white)}
.site-footer .brand{position:absolute;left:172px;top:150px}
.foot-col{position:absolute;top:80px}
.foot-col h3{font-family:"Montserrat",sans-serif;font-weight:700;font-size:16px;text-transform:uppercase;margin-bottom:18px}
.foot-col li{list-style:none;font-size:11px;line-height:22px}
.contact-row{display:flex;gap:14px;font-size:11px;line-height:17px;margin-bottom:22px;align-items:flex-start}
.foot-rule{position:absolute;left:172px;top:298px;width:856px;height:1px;background:#333}
.copyright{position:absolute;left:172px;top:330px;font-size:10px}
.social{position:absolute;left:866px;top:324px;display:flex;gap:30px}
.social span{width:18px;height:18px;border-radius:50%;border:2px solid var(--white)}
</style>
</head>
<body>

<header class="site-header abs">
  <div class="brand"><span class="brand-mark"></span>TESSLY REALTY</div>
  <nav class="main-nav">
    <a href="#">HOME</a><a href="#">ABOUT US</a><a href="#">SERVICES</a><a href="#">SIGN UP</a><a href="#">CONTACT</a>
  </nav>
</header>

<section class="hero abs" role="img" aria-label="Waterfront Florida villas with palm trees under a blue sky">
  <h1 class="hero-title">Assisting landlords increase<br>profits while decreasing the stress.</h1>
  <svg class="chev" style="left:28px;top:225px" width="24" height="50"><polyline points="22,2 2,25 22,48" fill="none" stroke="#fff" stroke-width="2"/></svg>
  <svg class="chev" style="right:28px;top:225px" width="24" height="50"><polyline points="2,2 22,25 2,48" fill="none" stroke="#fff" stroke-width="2"/></svg>
  <svg class="hero-slant" width="1200" height="62"><polygon points="0,62 1200,0 1200,62" fill="#fff"/></svg>
</section>

<h2 class="section-title" style="top:752px">How we can help</h2>
<div class="service" style="left:172px"><div class="photo" role="img" aria-label="Bright apartment dining room interior" style="background:linear-gradient(90deg,#f2f1ee 0%,#dcd8d1 40%,#c8b9a4 70%,#8f7a63 100%)"></div><p>Multi-family leasing</p></div>
<div class="service" style="left:465px"><div class="photo" role="img" aria-label="Brick apartment building facade with fire escapes" style="background:linear-gradient(180deg,#9fb0c2 0%,#7d6a5c 18%,#5e4c40 60%,#2e2723 100%)"></div><p>Multi-family sales</p></div>
<div class="service" style="left:759px"><div class="photo" role="img" aria-label="Aerial view of a coastal town and waterway" style="background:linear-gradient(180deg,#c3cdd8 0%,#8e9ba8 20%,#6f8161 45%,#55704a 75%,#7b8a6a 100%)"></div><p>Site selection advisory</p></div>

<section class="mortgage abs" role="img" aria-label="Dim city skyline with bridge at dusk">
  <h2 class="section-title">Mortgage calculator</h2>
  <div class="calc">
    <div class="field">Home Price</div>
    <div class="field">Down Payment</div>
    <div class="btn">CONTINUE</div>
  </div>
</section>

<div class="feature" style="left:172px;background:linear-gradient(180deg,#4f4a48 0%,#7a3a2a 25%,#6a2f24 55%,#2a2420 100%)" role="img" aria-label="Brooklyn brownstone row houses with stoops">
  <span class="label">Mortgage rates</span>
  <svg width="52" height="58" viewBox="0 0 52 58" fill="none" stroke="#fff" stroke-width="2"><rect x="4" y="36" width="9" height="20"/><rect x="20" y="28" width="9" height="28"/><rect x="36" y="18" width="9" height="38"/><polyline points="4,24 20,14 30,18 48,4"/><polyline points="40,4 48,4 48,12"/></svg>
</div>
<div class="feature" style="left:603px;background:linear-gradient(180deg,#3c4553 0%,#5a5f6a 30%,#6b4f4a 50%,#3a3a3e 75%,#2a2a2d 100%)" role="img" aria-label="Florida downtown street with mediterranean buildings">
  <span class="label">Coverage areas</span>
  <svg width="58" height="62" viewBox="0 0 58 62" fill="none" stroke="#fff" stroke-width="2"><path d="M29 46C18 32 14 26 14 18a15 15 0 0 1 30 0c0 8-4 14-15 28z"/><circle cx="29" cy="18" r="6"/><ellipse cx="29" cy="52" rx="26" ry="7"/></svg>
</div>

<section class="story abs">
  <div class="photo" role="img" aria-label="Brooklyn brick townhouse with iron railings" style="background:linear-gradient(90deg,#c9b58a 0%,#a48a62 28%,#7a4a3a 45%,#6a3e32 70%,#3a302c 100%)"></div>
  <div class="story-body">
    <h2>Our story</h2>
    <p>Tessly Realty NYC specializes in assisting landlords by increasing their profits while decreasing their stress. Tessly Realty NYC is a full service real estate brokerage firm located in Brooklyn, NY and West Palm Beach, FL. We specialize in assisting landlords by increasing their profits while decreasing their stress. Our firm concentrates on multifamily sales and leasing, distressed sales and 1031 Exchange property appropriation. With more than 12 years of experience in Brooklyn, we've narrowed our scope to its Northern and Eastern neighborhoods. Our West Palm Beach office specializes in Opportunity Zones in Palm Beach, Broward, Dade and Orange Counties</p>
    <span class="btn-outline">Contact us</span>
  </div>
</section>

<div class="ebook-body abs">
  <h2>Ebook for probate sales and multifamily leasing marketing campaigns</h2>
  <p>Sed ut perspiciatis unde omnis iste natus error sit voluptatem accusantium doloremque laudantium, totam rem aperiam, eaque ipsa quae ab illo inventore veritatis et quasi architecto beatae vitae dicta sunt explicabo. Nemo enim ipsam voluptatem quia voluptas sit aspernatur aut odit aut fugit, sed quia consequuntur magni dolores eos qui ratione voluptatem sequi nesciunt.</p>
  <span class="btn-outline">Download</span>
</div>
<div class="ebook-ring abs"></div>
<div class="ebook-cover abs" role="img" aria-label="Dark spiral-bound ebook cover"></div>

<section class="reviews abs" role="img" aria-label="Night city skyline">
  <h2 class="section-title">Reviews for Tessly Realty NYC</h2>
  <svg class="chev" style="left:135px;top:198px" width="36" height="76"><polyline points="34,2 2,38 34,74" fill="none" stroke="#fff" stroke-width="2"/></svg>
  <svg class="chev" style="right:135px;top:198px" width="36" height="76"><polyline points="2,2 34,38 2,74" fill="none" stroke="#fff" stroke-width="2"/></svg>
  <div class="stars">★★★★★</div>
  <div class="avatar" role="img" aria-label="Reviewer photo"></div>
  <p class="quote">Marcus is on point! I don't know how he does it, but whenever I have vacant apartments to rent, he finds me quality tenants extremely fast! He is honest with his feedback about how much rent to charge, how long it might take to rent out units, screening potential tenants, etc. Marcus is my go to real estate agent for Bedford Stuyvesant, Brooklyn.</p>
  <div class="reviewer"><span>-Rena T.</span><span>Brooklyn, NY</span></div>
</section>

<footer class="site-footer abs">
  <div class="brand"><span class="brand-mark"></span>TESSLY REALTY</div>
  <div class="foot-col" style="left:513px"><h3>Menu</h3><ul><li>Home</li><li>About us</li><li>Services</li><li>Sign up</li><li>Contact</li></ul></div>
  <div class="foot-col" style="left:655px"><h3>Links</h3><ul><li>Lorem ipsum dolor</li><li>Sit amet elit</li><li>Magna aliqua</li><li>Veniam quis</li><li>Tempor</li></ul></div>
  <div class="foot-col" style="left:838px"><h3>Contact us</h3>
    <div class="contact-row"><svg width="16" height="20" viewBox="0 0 16 20" fill="none" stroke="#fff" stroke-width="1.5"><path d="M8 19C3 12 1 9 1 7a7 7 0 0 1 14 0c0 2-2 5-7 12z"/><circle cx="8" cy="7" r="2.5"/></svg><span>1480 Linden Ave, 3, Brooklyn,<br>New York 11221</span></div>
    <div class="contact-row"><svg width="18" height="18" viewBox="0 0 18 18" fill="none" stroke="#fff" stroke-width="1.5"><path d="M4 1l3 4-2 2c1 2 3 4 6 6l2-2 4 3-2 3C8 17 1 10 1 3z"/></svg><span>Phone: 555-014-2270</span></div>
    <div class="contact-row"><svg width="18" height="14" viewBox="0 0 18 14" fill="none" stroke="#fff" stroke-width="1.5"><rect x="1" y="1" width="16" height="12"/><polyline points="1,1 9,8 17,1"/></svg><span>marcus@tesslyrealty.com</span></div>
  </div>
  <div class="foot-rule"></div>
  <div class="copyright">© 2019 All Rights Are Reserved Terms &amp; Conditions</div>
  <div class="social" aria-label="Social links"><span></span><span></span><span></span><span></span></div>
</footer>

</body>
</html>
```